Suds Haven Laundromat Wordpress Design

We need a Wordpress website design for our laundromat, Suds Haven Atlanta, at www.sudshavenatlanta-example.com. We would like to have 6 pages: Home, About Us, Services, Locations, Reviews and Contact us. We will provide content for the text on each page. What we do: We are a full service laundromat that provides dry cleaning drop off, professional laundry services, wash dry fold and self service laundry to the local community. We would like to use the color scheme from our logo to convey a warm, safe, and bright business that caters to its diverse community.
Updates

I like the structure of this laundromat website: http://www.washtroveusa-example.com/ Using my logo and color scheme in the above referenced website is what. Am looking for. The photos attached to the project with the female model should be used as a primary focus and supplemented by actual photos of the equipment.

Target Market(s)

Our target market is a diverse group of people from Midtown Atlanta - LGBTQ community /Locals/Regulars that have been coming to laundromat for 30 years.

Industry/Entity Type

Laundromat

Coding

Coded - Design and coding required

Number of Pages Required

5+ page

Font styles to use
Sans Serif

Colors
0054AA
0677BA
7BADD7
CADEEF
E8F1F8

Requirements
Must have
• Feature this video on the main page: https://videohost-example.com/xq7Rm2bPz4k

```html
<!DOCTYPE html>
<html lang="en">
<head>
<meta charset="utf-8">
<title>Suds Haven – Full Service Laundromat</title>
<link rel="stylesheet" href="https://fonts.googleapis.com/css2?family=Montserrat:wght@300;400;500;600;700;800;900&display=swap">
<style>
:root{
  --blue:#0054aa;
  --blue-deep:#0b3f95;
  --blue-mid:#0677ba;
  --blue-soft:#7badd7;
  --blue-pale:#cadeef;
  --blue-mist:#e8f1f8;
  --ink:#1b1b1b;
  --grey:#6b6b6b;
  --star:#f5a300;
  --white:#fff;
}
*{margin:0;padding:0;box-sizing:border-box}
html,body{width:1200px;height:3069px;overflow:hidden}
body{position:relative;font-family:'Montserrat',sans-serif;color:var(--ink);background:var(--white)}
.abs{position:absolute}
.hero{left:0;top:0;width:1200px;height:730px;background:
  radial-gradient(ellipse at 50% 30%,#a9c7c4 0%,#7f9893 35%,#4d5654 70%,#2c3130 100%)}
.header{left:111px;top:26px;width:977px;height:87px;background:var(--white);box-shadow:0 2px 10px rgba(0,0,0,.2);display:flex;align-items:center;padding:0 19px 0 22px}
.brand{display:flex;align-items:center;gap:10px;font-weight:700;font-size:26px;color:var(--blue-mid);letter-spacing:.5px}
.brand-dot{width:30px;height:30px;border-radius:50%;background:var(--blue-mid)}
.nav{margin-left:auto;display:flex;gap:37px;font-size:14.5px;font-weight:500}
.btn{display:inline-flex;align-items:center;justify-content:center;gap:12px;background:var(--blue);color:var(--white);font-size:14.5px;font-weight:500}
.header .btn{margin-left:35px;width:134px;height:36px}
.stars{display:flex;gap:6px}
.hero-title{left:176px;top:417px;width:778px;height:84px;background:var(--blue-deep);color:var(--white);font-weight:900;font-size:92px;line-height:84px;letter-spacing:2px;text-align:center}
.hero-laundry{left:480px;top:498px;font-size:72px;font-weight:900;letter-spacing:21px;color:var(--blue-deep);line-height:72px;
  text-shadow:2px 0 0 #fff,-2px 0 0 #fff,0 2px 0 #fff,0 -2px 0 #fff,1.5px 1.5px 0 #fff,-1.5px -1.5px 0 #fff,1.5px -1.5px 0 #fff,-1.5px 1.5px 0 #fff}
.hero-services{left:646px;top:560px;font-size:50px;font-weight:600;color:var(--white);line-height:50px}
.hero .cta{left:763px;top:618px;width:193px;height:38px;font-size:13px;letter-spacing:1.5px}
.watermark{font-weight:900;color:var(--blue-mist);font-size:64px;letter-spacing:5px;text-align:center;line-height:1}
.section-sub{font-size:27px;font-weight:500;text-align:center;width:1200px;left:0}
.section-title{font-size:40px;font-weight:600;text-align:center;width:1200px;left:0}
.card{top:937px;width:302px;height:362px;overflow:hidden}
.card .label{position:absolute;left:0;right:0;bottom:22px;text-align:center;color:var(--white);font-weight:800;font-size:17px;line-height:31px}
.card svg{position:absolute;left:0;top:0}
.about{left:0;top:1488px;width:1200px;height:584px;background:linear-gradient(180deg,#e4eef8,#dce8f4)}
.about-copy{left:111px;top:180px;width:476px}
.about p{font-size:13.2px;line-height:25px;color:#444;font-weight:300}
.about-copy .btn{margin-top:22px;width:193px;height:37px;font-size:13px;letter-spacing:1.5px}
.review{top:2334px;width:485px;height:252px;text-align:center;padding:31px 45px 0}
.review .quote{font-size:12.5px;line-height:20px;color:var(--grey);margin-top:14px}
.review .rule{width:40px;height:2px;background:var(--blue);margin:20px auto 14px}
.review .name{font-size:18px;color:var(--blue);font-weight:500}
.review .place{font-size:12px;color:#444;margin-top:2px}
.footer{left:0;top:2703px;width:1200px;height:366px;background:var(--blue-deep);color:var(--white)}
.footer h4{font-size:16px;font-weight:600;letter-spacing:.5px}
.footer .item{display:flex;gap:16px;font-size:13px;font-weight:500;line-height:20px}
.footer .divider{width:1px;background:rgba(255,255,255,.3)}
.social{width:30px;height:30px;border:1.5px solid var(--white);border-radius:50%}
.footer .bottom{font-size:12.5px;color:#a9c3ea}
</style>
</head>
<body>
<svg width="0" height="0" style="position:absolute">
  <defs>
    <symbol id="star" viewBox="0 0 24 24"><path fill="#f5a300" d="M12 1.5l3.2 6.9 7.5.9-5.6 5.1 1.5 7.5L12 18.1l-6.6 3.8 1.5-7.5L1.3 9.3l7.5-.9z"/></symbol>
    <symbol id="pin" viewBox="0 0 24 24"><path fill="currentColor" d="M12 2a7 7 0 0 0-7 7c0 5 7 13 7 13s7-8 7-13a7 7 0 0 0-7-7zm0 9.5A2.5 2.5 0 1 1 12 6.5a2.5 2.5 0 0 1 0 5z"/></symbol>
  </defs>
</svg>

<section class="abs hero" role="img" aria-label="Photo of a woman in a blue dress walking between rows of laundromat washers, with a retro painted sign above">
  <div class="abs stars" style="left:235px;top:388px"><svg width="26" height="26"><use href="#star"/></svg><svg width="26" height="26"><use href="#star"/></svg><svg width="26" height="26"><use href="#star"/></svg><svg width="26" height="26"><use href="#star"/></svg><svg width="26" height="26"><use href="#star"/></svg></div>
  <div class="abs hero-title">PROFESSIONAL</div>
  <div class="abs hero-laundry">LAUNDRY</div>
  <div class="abs hero-services">SERVICES</div>
  <a class="abs btn cta">GET STARETED NOW</a>
</section>

<header class="abs header">
  <div class="brand"><span class="brand-dot"></span>Suds Haven</div>
  <nav class="nav"><span>Home</span><span>About Us</span><span>Services</span><span>Reviews</span><span>Contact Us</span></nav>
  <a class="btn"><svg width="16" height="16"><use href="#pin"/></svg>Locations</a>
</header>

<div class="abs watermark" style="left:0;width:1200px;top:806px">WHAT WE DO</div>
<div class="abs section-sub" style="top:842px">We Are A Full Service</div>
<div class="abs section-title" style="top:872px">Laundromat That Provides</div>

<div class="abs card" style="left:111px;background:linear-gradient(160deg,#c9c9c4,#7c7d7a)" role="img" aria-label="Row of stainless steel dryers">
  <svg width="302" height="362" viewBox="0 0 302 362"><path d="M0 362V300C22 235 80 205 135 208C190 212 210 265 302 275V362Z" fill="#000"/><path d="M0 300C22 235 80 205 135 208C190 212 210 265 302 275" fill="none" stroke="#0b3f95" stroke-width="5"/></svg>
  <div class="label">DRY CLEANING<br>DROP OFF</div>
</div>
<div class="abs card" style="left:449px;background:linear-gradient(160deg,#9fc8bf,#6b7a74)" role="img" aria-label="Laundromat interior with washers and plants">
  <svg width="302" height="362" viewBox="0 0 302 362"><path d="M0 362V280C40 220 120 205 160 212C220 222 230 200 302 222V362Z" fill="#0b3f95"/></svg>
  <div class="label">PROFESSIONAL LAUNDRY<br>SERVICES</div>
</div>
<div class="abs card" style="left:786px;background:linear-gradient(160deg,#e3e3e6,#9aa0aa)" role="img" aria-label="Two attendants holding folded towels">
  <svg width="302" height="362" viewBox="0 0 302 362"><path d="M0 362V290C22 235 80 205 135 208C190 212 210 265 302 275V362Z" fill="#000"/><path d="M0 290C22 235 80 205 135 208C190 212 210 265 302 275" fill="none" stroke="#0b3f95" stroke-width="5"/></svg>
  <div class="label">WASH DRY FOLD AND<br>SELF SERVICE LAUNDRY</div>
</div>
<a class="abs btn" style="left:533px;top:1348px;width:133px;height:37px"><svg width="16" height="16"><use href="#pin"/></svg>Locations</a>

<section class="abs about">
  <div class="abs watermark" style="left:92px;top:92px;color:#d2e1f0;text-align:left">WHO WE ARE</div>
  <div class="abs" style="left:111px;top:128px;font-size:27px;font-weight:500">About Our Company</div>
  <div class="abs about-copy">
    <p>Lorem Ipsum is simply dummy text of the printing and typesetting industry. Lorem Ipsum has been the industry's standard dummy text ever since the 1500s, when an unknown printer took a galley of type and scrambled it to make a type specimen book.</p>
    <p style="margin-top:25px">It has survived not only five centuries, but also the leap into electronic typesetting, remaining essentially unchanged. It was popularised in the 1960s with the release of Letraset sheets containing Lorem Ipsum passages, and more recently with desktop publishing software like Aldus PageMaker including versions of Lorem Ipsum.</p>
    <a class="btn">GET STARETED NOW</a>
  </div>
  <svg class="abs" style="left:570px;top:20px" width="540" height="540" viewBox="0 0 540 540">
    <path d="M270 20C380 5 500 80 510 230C520 400 420 500 260 500C120 500 20 400 40 260C50 120 150 35 270 20Z" fill="#7badd7"/>
    <path d="M260 40C370 30 470 110 475 250C480 390 390 480 250 478C130 476 30 390 45 250C58 130 150 50 260 40Z" fill="#cadeef"/>
    <circle cx="400" cy="45" r="8" fill="#7badd7"/><circle cx="495" cy="115" r="10" fill="#7badd7"/><circle cx="400" cy="510" r="13" fill="#7badd7"/><circle cx="470" cy="50" r="36" fill="#7badd7"/>
  </svg>
  <div class="abs" style="left:599px;top:54px;width:476px;height:476px;border-radius:50%;background:linear-gradient(160deg,#cfcfca,#8e918f)" role="img" aria-label="Video still: woman in a blue dress seated in front of washers"></div>
  <div class="abs" style="left:807px;top:262px;width:60px;height:60px;border-radius:50%;background:#fff;box-shadow:0 2px 8px rgba(0,0,0,.3)">
    <svg width="60" height="60" viewBox="0 0 60 60"><path d="M23 17L43 30 23 43Z" fill="#e21b1b"/></svg>
  </div>
</section>

<div class="abs watermark" style="left:0;width:1200px;top:2180px">REVIEWS</div>
<div class="abs section-sub" style="top:2212px">What Our Happy</div>
<div class="abs section-title" style="top:2243px">Customers Say About Us</div>

<div class="abs review" style="left:111px;background:var(--blue-mist)">
  <div class="stars" style="justify-content:center;gap:4px"><svg width="18" height="18"><use href="#star"/></svg><svg width="18" height="18"><use href="#star"/></svg><svg width="18" height="18"><use href="#star"/></svg><svg width="18" height="18"><use href="#star"/></svg><svg width="18" height="18"><use href="#star"/></svg></div>
  <p class="quote">"Lorem Ipsum is simply dummy text of the printing and typesetting industry. Lorem Ipsum has been the industry's standard dummy text ever since the 1500s, when an unknown printer took a galley of type and scrambled it to make a type specimen book. It has survived not only five centuries,"</p>
  <div class="rule"></div><div class="name">Maria L Bennett</div><div class="place">Midtown</div>
</div>
<div class="abs review" style="left:604px;background:#fff;box-shadow:0 0 10px rgba(0,0,0,.12)">
  <div class="stars" style="justify-content:center;gap:4px"><svg width="18" height="18"><use href="#star"/></svg><svg width="18" height="18"><use href="#star"/></svg><svg width="18" height="18"><use href="#star"/></svg><svg width="18" height="18"><use href="#star"/></svg><svg width="18" height="18"><use href="#star"/></svg></div>
  <p class="quote">"Lorem Ipsum is simply dummy text of the printing and typesetting industry. Lorem Ipsum has been the industry's standard dummy text ever since the 1500s, when an unknown printer took a galley of type and scrambled it to make a type specimen book. It has survived not only five centuries,"</p>
  <div class="rule"></div><div class="name">Maria L Bennett</div><div class="place">Midtown</div>
</div>

<footer class="abs footer">
  <svg class="abs" style="left:0;top:0" width="1200" height="366"><path d="M0 300C150 250 300 330 420 366H0Z" fill="#0a3a8a"/><path d="M800 0C900 80 1050 60 1200 120V0Z" fill="#0d4aa3"/></svg>
  <h4 class="abs" style="left:111px;top:47px">CONTACT US</h4>
  <div class="abs item" style="left:111px;top:85px"><svg width="18" height="20"><use href="#pin"/></svg><span>820 Juniper Row, Midtown<br>Georgia, 30308.</span></div>
  <div class="abs item" style="left:111px;top:143px"><svg width="18" height="18" viewBox="0 0 24 24"><path fill="#fff" d="M6.6 10.8a15 15 0 0 0 6.6 6.6l2.2-2.2a1 1 0 0 1 1-.25 11.4 11.4 0 0 0 3.6.57 1 1 0 0 1 1 1V20a1 1 0 0 1-1 1A17 17 0 0 1 3 4a1 1 0 0 1 1-1h3.5a1 1 0 0 1 1 1c0 1.250.2 2.45.57 3.57a1 1 0 0 1-.25 1z"/></svg><span>Phone:<br>404-555-0182</span></div>
  <div class="abs item" style="left:111px;top:196px"><svg width="18" height="18" viewBox="0 0 24 24"><path fill="#fff" d="M3 5h18v14H3zm2 2v.5l7 4.5 7-4.5V7z"/></svg><span>Email:<br>info@sudshaven-example.com</span></div>
  <div class="abs divider" style="left:412px;top:50px;height:197px"></div>
  <div class="abs brand" style="left:448px;top:104px;color:#fff;font-size:30px"><span class="brand-dot" style="background:#fff"></span>Suds Haven</div>
  <div class="abs" style="left:507px;top:200px;display:flex;gap:5px"><span class="social"></span><span class="social"></span><span class="social"></span><span class="social"></span></div>
  <div class="abs divider" style="left:744px;top:50px;height:197px"></div>
  <h4 class="abs" style="left:785px;top:47px">SIGN UP FOR NEWSLETTER</h4>
  <p class="abs" style="left:785px;top:87px;width:300px;font-size:13px;line-height:24px;color:#d5e2f5">Excepteur sint occaecat cupidatat non proident, sunt in culpa qui officia deserunt</p>
  <div class="abs" style="left:785px;top:144px;width:303px;height:47px;background:#fff;color:#333;font-size:11.5px;font-weight:500;padding:16px 21px">Enter email</div>
  <div class="abs btn" style="left:785px;top:201px;width:151px;height:42px;background:var(--blue-mid);font-size:15px;font-weight:600">SUBSCRIBE</div>
  <div class="abs" style="left:111px;top:286px;width:977px;height:1px;background:rgba(255,255,255,.2)"></div>
  <div class="abs bottom" style="left:111px;top:312px">Home &nbsp;|&nbsp; About Us &nbsp;|&nbsp; Services &nbsp;|&nbsp; Reviews &nbsp;|&nbsp; Contact Us</div>
  <div class="abs bottom" style="right:112px;top:312px">© 2021 All Rights Reserved | Privacy Policy | Terms and Conditions</div>
</footer>
</body>
</html>
```